Volbrey Inc Business Card

Looking to get an updated business card for a Contract Machining company (www.volbreyinc.example) - looking for a clean design the portrays the technical nature of the business - colors can follow the website design and be in any combination that makes sense (red black, white, metallic or silver) - logos attached for use also. Would like space for: Name, title, business phone (555 214-3086), cell phone , website (www.volbreyinc.example) - possibly QR code could be integrated for website (designer choice), business address - 418 Harlow Bend, Larkhaven, MN 48199 (cards will be for 4 employees, I will either need to modify a template or I can provide individual information)
Target Market(s)
Aerospace, defense and medical device manufacturing companies that need machining
Industry/Entity Type
Machining for aerospace, defense, medical
Contact Information for Business Card
Name, Title, Business Phone, Cell Phone, email, business website and business address
Look and feel

```html
<!DOCTYPE html>
<html lang="en">
<head>
<meta charset="utf-8">
<title>Volbrey Inc Business Card</title>
<link href="https://fonts.googleapis.com/css2?family=Montserrat:wght@700&family=Arimo:wght@400;700&display=swap" rel="stylesheet">
<style>
  :root {
    --brand-red: #b01e24;
    --paper-white: #ffffff;
    --backdrop: #2a2a2c;
  }
  * { box-sizing: border-box; margin: 0; padding: 0; }
  html, body { width: 1200px; height: 874px; overflow: hidden; }
  body {
    background: var(--backdrop);
    position: relative;
    font-family: "Arimo", Arial, sans-serif;
  }
  .card {
    position: absolute;
    left: 280px;
    width: 640px;
    height: 366px;
    border-radius: 22px;
    overflow: hidden;
  }
  .card-back { top: 40px; background: var(--brand-red); }
  .card-front { top: 460px; background: var(--paper-white); }

  .back-mark {
    position: absolute;
    left: 50%;
    top: 70px;
    width: 150px;
    height: 150px;
    margin-left: -75px;
    border-radius: 50%;
    background: var(--paper-white);
  }
  .back-name {
    position: absolute;
    left: 0; right: 0;
    top: 240px;
    text-align: center;
    font-family: "Montserrat", Arial, sans-serif;
    font-weight: 700;
    font-size: 38px;
    letter-spacing: 1px;
    color: var(--paper-white);
    text-transform: uppercase;
  }

  .front-shape { position: absolute; inset: 0; }
  .front-info {
    position: absolute;
    right: 36px;
    top: 34px;
    text-align: right;
    color: var(--paper-white);
  }
  .front-name {
    font-family: "Montserrat", Arial, sans-serif;
    font-weight: 700;
    font-size: 32px;
    letter-spacing: 1px;
    text-transform: uppercase;
    margin-bottom: 26px;
  }
  .person { font-weight: 700; font-size: 24px; }
  .title { font-size: 15px; margin-bottom: 16px; }
  .address { font-size: 15px; line-height: 1.25; margin-bottom: 16px; }
  .contact-list { list-style: none; font-size: 15px; line-height: 1.4; }
  .contact-list li { display: flex; justify-content: flex-end; align-items: center; gap: 8px; }
  .contact-list svg { width: 13px; height: 13px; fill: var(--paper-white); }
</style>
</head>
<body>
  <section class="card card-back">
    <div class="back-mark"></div>
    <div class="back-name">Volbrey Inc</div>
  </section>

  <section class="card card-front">
    <svg class="front-shape" viewBox="0 0 640 366" aria-hidden="true">
      <circle cx="215" cy="195" r="200" fill="var(--brand-red)"/>
      <rect x="215" y="0" width="425" height="366" fill="var(--brand-red)"/>
      <circle cx="195" cy="190" r="165" fill="none" stroke="var(--paper-white)" stroke-width="3"/>
    </svg>
    <div class="front-info">
      <div class="front-name">Volbrey Inc</div>
      <div class="person">Marek Halden</div>
      <div class="title">President</div>
      <div class="address">418 Harlow Bend<br>Larkhaven, MN 48199</div>
      <ul class="contact-list">
        <li>555 214-3086
          <svg viewBox="0 0 24 24"><path d="M6.6 10.8a15.1 15.1 0 0 0 6.6 6.6l2.2-2.2a1 1 0 0 1 1-.25 11.4 11.4 0 0 0 3.6.57 1 1 0 0 1 1 1V20a1 1 0 0 1-1 1A17 17 0 0 1 3 4a1 1 0 0 1 1-1h3.5a1 1 0 0 1 1 1c0 1.250.2 2.450.57 3.57a1 1 0 0 1-.25 1z"/></svg></li>
        <li>555 307-4412
          <svg viewBox="0 0 24 24"><path d="M7 1h10a2 2 0 0 1 2 2v18a2 2 0 0 1-2 2H7a2 2 0 0 1-2-2V3a2 2 0 0 1 2-2zm0 3v15h10V4z"/></svg></li>
        <li>info@volbreyinc.example
          <svg viewBox="0 0 24 24"><path d="M2 5h20v14H2zm2 2v.5l8 5 8-5V7z"/></svg></li>
        <li>www.volbreyinc.example
          <svg viewBox="0 0 24 24"><circle cx="12" cy="12" r="10"/></svg></li>
      </ul>
    </div>
  </section>
</body>
</html>
```